Business card design Needed for new logo / Construction business, home extensions and new builds

We need a business card design using our new logo files which i will attach to this project :)

We are a small construction business specialising in home extensions, new builds and property development. We are very ambitious and would appreciate professional and elegant designs for our new business card.

Very serious about using the services on MakerQuarry and recently acquired our new logo from here :)

Please get involved, i will feedback when i can as i am very busy but can respond daily, thanks

Target Market(s)

People that want to build onto their houses, new building developments or adding too their existing property

Industry/Entity Type

Construction

Contact Information for Business Card

Renwick Tolliver Construction, Lionel Ashby (Managing Director), Tel 07822254961, email - info@renwick-tolliver, www.renwick-tolliver.co.uk

Colors

Designer to choose colors to be used in the design.

Requirements
Must have
• I like a deep grey on the back please. A lot of you have provided black from and back, try mixing things up a little. The black looks cool 😎 Thanks

```html
<!DOCTYPE html>
<html lang="en">
<head>
<meta charset="UTF-8">
<title>Renwick Tolliver Construction — Business Card</title>
<link rel="stylesheet" href="https://fonts.googleapis.com/css2?family=Cinzel:wght@500&family=Open+Sans:wght@400;600;700&display=swap">
<style>
  :root {
    --page: #1b1b1e;
    --card-back: #1f1f24;
    --card-front: #1c1c21;
    --gold: #e0a52a;
    --gold-light: #f2c14e;
    --silver: #c9cacd;
    --white: #f3f3f3;
    --emboss: #26262c;
    --emboss-edge: #2f2f36;
  }
  * { margin: 0; padding: 0; box-sizing: border-box; }
  html, body {
    width: 1200px; height: 780px; overflow: hidden;
    background: var(--page);
  }
  .canvas {
    position: relative; width: 1200px; height: 780px;
    display: flex; align-items: center; justify-content: center; gap: 40px;
  }
  .card {
    position: relative; width: 530px; height: 303px; overflow: hidden;
    box-shadow: 0 14px 30px rgba(0,0,0,.55);
  }

  /* Back side */
  .card--back {
    background: var(--card-back);
    border-left: 2px solid var(--gold);
    border-bottom: 3px solid var(--gold);
  }
  .card--back .emboss-name {
    position: absolute; left: 0; right: 0; top: 50%;
    transform: translateY(-50%);
    text-align: center;
    font-family: "Cinzel", serif; font-weight: 500;
    font-size: 30px; line-height: 1.25; letter-spacing: 2px;
    color: var(--emboss);
    text-shadow: 0 1px 0 var(--emboss-edge), 0 -1px 0 #121215;
  }

  /* Front side */
  .card--front {
    background: var(--card-front);
    border-left: 2px solid var(--gold);
    border-bottom: 3px solid var(--gold);
  }
  .gold-tab {
    position: absolute; top: 0; right: 0; width: 16px; height: 62px;
    background: linear-gradient(180deg, var(--gold-light), var(--gold));
  }
  .person {
    position: absolute; top: 20px; right: 30px; text-align: right;
    font-family: "Open Sans", sans-serif;
  }
  .person__name { font-size: 27px; font-weight: 700; color: var(--silver); line-height: 1.1; }
  .person__name .surname { color: var(--gold-light); }
  .person__role { font-size: 13px; font-weight: 600; color: var(--white); margin-top: 2px; }

  .decor-name {
    position: absolute; right: 26px; top: 96px; text-align: right;
    font-family: "Cinzel", serif; font-weight: 500;
    font-size: 34px; line-height: 1.1;
    color: #141418;
    text-shadow: 0 1px 0 #26262c;
  }

  .company {
    position: absolute; left: 30px; bottom: 118px;
    display: flex; align-items: center; gap: 10px;
  }
  .company__mark { width: 12px; height: 12px; background: var(--gold); }
  .company__name {
    font-family: "Cinzel", serif; font-weight: 500;
    font-size: 17px; line-height: 1.2; letter-spacing: 1px;
    color: var(--silver);
  }

  .contact {
    position: absolute; left: 30px; bottom: 22px;
    font-family: "Open Sans", sans-serif; font-size: 13px; color: var(--white);
    line-height: 1.35;
  }
  .contact__address { margin-bottom: 8px; }
  .contact__row { display: flex; align-items: center; gap: 8px; }
  .contact__row svg { width: 12px; height: 12px; fill: var(--gold); flex: none; }
</style>
</head>
<body>
<main class="canvas">

  <section class="card card--back" aria-label="Card back">
    <p class="emboss-name">Renwick Tolliver<br>Construction</p>
  </section>

  <section class="card card--front" aria-label="Card front">
    <span class="gold-tab"></span>
    <div class="person">
      <p class="person__name">Lionel <span class="surname">Ashby</span></p>
      <p class="person__role">Managing Director</p>
    </div>

    <p class="decor-name" aria-hidden="true">Renwick<br>Tolliver</p>

    <div class="company">
      <span class="company__mark"></span>
      <p class="company__name">Renwick Tolliver<br>Construction</p>
    </div>

    <div class="contact">
      <p class="contact__address">Ashcombe Lane, Hollowdene<br>Harrowmere, HX4 7LT</p>
      <p class="contact__row">
        <svg viewBox="0 0 24 24" aria-hidden="true"><path d="M6.6 10.8a15.1 15.1 0 0 0 6.6 6.6l2.2-2.2c.3-.3.7-.4 1-.2 1.1.4 2.3.6 3.6.6.6 0 1 .4 1 1V20c0 .6-.4 1-1 1A17 17 0 0 1 3 4c0-.6.4-1 1-1h3.5c.6 0 1 .4 1 1 0 1.3.2 2.5.6 3.6.1.3 0 .7-.2 1z"/></svg>
        0782 225 4961
      </p>
      <p class="contact__row">
        <svg viewBox="0 0 24 24" aria-hidden="true"><path d="M3 5h18v14H3zm2 2v.4l7 4.6 7-4.6V7zm0 2.8V17h14V9.8l-7 4.6z"/></svg>
        info@renwick-tolliver.co.uk
      </p>
      <p class="contact__row">
        <svg viewBox="0 0 24 24" aria-hidden="true"><path d="M12 2a10 10 0 1 0 0 20 10 10 0 0 0 0-20zm6.9 6h-3a15.6 15.6 0 0 0-1.3-3.9A8 8 0 0 1 18.9 8zM12 4c.8 1.1 1.5 2.5 1.9 4h-3.8c.4-1.5 1.1-2.9 1.9-4zM4.3 14a8 8 0 0 1 0-4h3.4a16 16 0 0 0 0 4zm.8 2h3a15.6 15.6 0 0 0 1.3 3.9A8 8 0 0 1 5.1 16zm3-8h-3a8 8 0 0 1 4.3-3.9A15.6 15.6 0 0 0 8.1 8zM12 20c-.8-1.1-1.5-2.5-1.9-4h3.8c-.4 1.5-1.1 2.9-1.9 4zm2.3-6H9.7a14.7 14.7 0 0 1 0-4h4.6a14.7 14.7 0 0 1 0 4zm.3 5.9a15.6 15.6 0 0 0 1.3-3.9h3a8 8 0 0 1-4.3 3.9zm1.7-5.9a16 16 0 0 0 0-4h3.4a8 8 0 0 1 0 4z"/></svg>
        www.renwick-tolliver.co.uk
      </p>
    </div>
  </section>

</main>
</body>
</html>
```